"Velmora Crest" sexual performance enhancement pill bottle label needed.

This should be interesting...

I am starting a line of sexual performance enhancement products. This will be the first of several products basically. Keep in mind, I am the type of business person to stay with one company for years if they provide me with quality work.

This particular product is a male sexual performance pill. The name of the product is "Velmora Crest." The packaging of the pills are a black bottle with a white top. Label on the product example would be perfect but at a minimum I have attached a "template" for your guidance.

Some of the technical aspects of this are as follows:

-File Format: Illustrator CS6 is preferred. (Winner must provide artwork in layer and can not flatten artwork.)
-Resolution: 300 dpi minimum
-Bleed: 1/16th (0.0625") inch from edge of label
-Color Mode: CMYK only or must be converted to CMYK for final production

Lastly, this is your project as a designer, artist, creator, this is essentially a piece of you that will be sold and known by thousands of people. I have no color scheme that I prefer, just use the template and follow the layout. If you have any further questions, please feel free to contact me at any time.
Updates

Quick note on the product and what it does: -Powerful, long lasting, harder erections -Works in a minutes and last for hours -Enhances sexual desire and drive Thank you for your ideas...

Project Deadline Extended
Reason: We decided to extent the project for a few more days to let the last few concepts come in. So far things are looking really good and we definitely have seen some amazing designs. Thank you for your hard work and amazing creativity. Looking forward to seeing what we have come in the next couple of day. Very respectfully, Brev

ONLY THREE DAYS LEFT!!!! Please submit your ideas as soon as possible. And as always, thank you for your help!!! V/r, Brev

Industry/Entity Type

Graphic Design

```html
<!DOCTYPE html>
<html lang="en">
<head>
<meta charset="utf-8">
<title>Velmora Crest – Bottle Label</title>
<link rel="stylesheet" href="https://fonts.googleapis.com/css2?family=Oswald:wght@400;600;700&family=Roboto+Condensed:wght@400;700&display=swap">
<style>
:root{
  --backdrop:#c8c8c8;
  --label:#000000;
  --ink:#ffffff;
  --ink-soft:#e6e6e6;
  --muted:#7a7a7a;
  --accent:#e3122b;
  --title:#1a1a1a;
  --gold:#e0a31c;
  --gold-light:#f6d25a;
}
*{margin:0;padding:0;box-sizing:border-box}
html,body{width:1200px;height:681px;overflow:hidden;background:var(--backdrop)}
.canvas{position:relative;width:1200px;height:681px;background:var(--backdrop)}
.label{position:absolute;left:81px;top:114px;width:1036px;height:411px;background:var(--label);border-radius:17px;color:var(--ink);font-family:"Roboto Condensed",sans-serif}
.directions{position:absolute;left:20px;top:28px;width:225px;font-size:8.4px;line-height:1.3;text-align:justify}
.directions p{margin-bottom:6px}
.directions .disclaimer{margin-top:12px}
.quality-seal{position:absolute;left:324px;top:89px;width:70px;height:70px}
.hero{position:absolute;left:429px;top:24px;width:332px;height:158px;background:#fff;overflow:hidden}
.hero-photo{position:absolute;left:0;top:0;width:150px;height:158px;background:linear-gradient(90deg,#0c0c0c 0%,#3a3a3a 45%,#c9c9c9 80%,#ffffff 100%)}
.brand-name{position:absolute;left:130px;top:14px;width:195px;font-family:"Oswald",sans-serif;font-weight:700;color:var(--title);font-size:52px;line-height:1.04;letter-spacing:-0.5px;text-transform:uppercase;text-align:center}
.claims{position:absolute;left:0;top:190px;width:1036px;font-family:"Oswald",sans-serif;text-transform:uppercase}
.claims-left{position:absolute;right:527px;top:0;text-align:right;font-weight:400;font-size:23px;line-height:27px;color:var(--ink)}
.claims-right{position:absolute;left:514px;top:0;font-weight:700;font-size:23px;line-height:27px;letter-spacing:1.5px;color:var(--muted)}
.divider{position:absolute;left:14px;right:24px;top:289px;height:3px;background:var(--ink)}
.promise{position:absolute;left:0;width:1024px;top:300px;text-align:center;font-size:15px;font-weight:700;color:var(--accent);letter-spacing:.2px}
.maker{position:absolute;left:23px;top:336px;font-size:13px;line-height:17px}
.count{position:absolute;left:516px;top:366px;font-family:"Oswald",sans-serif;font-weight:700;color:var(--muted);font-size:21px}
.count span{font-size:11px;margin-left:2px}
.facts{position:absolute;left:795px;top:24px;width:217px}
.facts h2{font-family:"Oswald",sans-serif;font-weight:400;font-size:26px;line-height:30px}
.facts .serving{font-size:11.5px;line-height:15px;margin-top:2px}
.facts .rule-thick{height:3px;background:var(--ink);margin:6px 0 4px}
.facts .row{display:flex;justify-content:space-between;font-size:10px;line-height:13px}
.facts .rule-thin{height:1.5px;background:var(--ink);margin:4px 0 6px}
.facts .blend{font-size:9.6px;line-height:12.4px;text-align:justify}
.facts .blend .row{margin-bottom:1px;font-weight:700}
.footnote{position:absolute;left:795px;top:322px;font-size:11px}
.other{position:absolute;left:795px;top:357px;width:217px;font-size:10.5px;line-height:13.5px}
</style>
</head>
<body>
<div class="canvas">
  <section class="label">
    <div class="directions">
      <p>SUGGESTED USE: As a dietary supplement, take two (2) capsules 1 hour before physical activity, or as directed by your health care professional. Do not exceed two (2) capsules daily.</p>
      <p>CAUTION: Do not exceed recommended dose. This product is not intended for pregnant or nursing mothers, children under the age of 18, or individuals taking prescription drugs. Discontinue use immediately if nausea, sleeplessness, or nervousness occur. Do not take this product if you have a known medical condition including high blood pressure, diabetes, any cardiovascular disorder, heart disease, hyperthyroidism, or are taking anti-depressant medications. If you have questions about the advisability of taking this product, consult your physician prior to use.</p>
      <p class="disclaimer">KEEP OUT OF THE REACH OF CHILDREN. DO NOT USE IF SAFETY SEAL IS DAMAGED OR MISSING. STORE AT ROOM TEMPERATURE.</p>
      <p>* These statements have not been evaluated by the Food and Drug Administration. This product is not intended to diagnose, treat, cure or prevent any disease.</p>
    </div>

    <svg class="quality-seal" viewBox="0 0 70 70" aria-hidden="true">
      <defs>
        <radialGradient id="sealGold" cx="40%" cy="35%" r="65%">
          <stop offset="0" stop-color="var(--gold-light)"/>
          <stop offset="1" stop-color="var(--gold)"/>
        </radialGradient>
      </defs>
      <circle cx="35" cy="35" r="33" fill="url(#sealGold)"/>
    </svg>

    <div class="hero">
      <div class="hero-photo" role="img" aria-label="Photo of a couple about to kiss, in black and white"></div>
      <div class="brand-name">Velmora<br>Crest</div>
    </div>

    <div class="claims">
      <div class="claims-left">Powerful<br>Long Lasting<br>Harder Erections</div>
      <div class="claims-right">Enhances<br>Sexual Desire<br>And Drive</div>
    </div>

    <div class="divider"></div>
    <p class="promise">WORKS IN A MINUTES AND LAST FOR HOURS</p>

    <div class="maker">Manufactured Exclusively For:<br>COMPANY INFO</div>
    <div class="count">60<span>TABLETS</span></div>

    <div class="facts">
      <h2>Supplement Facts</h2>
      <p class="serving">Serving Size: 2 Capsules<br>Servings Per Container: 30</p>
      <div class="rule-thick"></div>
      <div class="row"><span>Amount Per Serving</span><span>% Daily Value</span></div>
      <div class="rule-thin"></div>
      <div class="blend">
        <div class="row"><span>VLC-Rx™ Proprietary Formula</span><span>1,560 mg &nbsp;†</span></div>
        Horny Goat Weed (herb powder), Maca (herb powder), Macuna Pruriens (L-Dopa), Polypodium Vulgare (herb powder), Yohimbe Bark (herb powder), Saw Palmetto (herb powder), Muira Puama (herb powder), Arginine (L-Arginine hydrochloride), Panax Ginseng (herb powder)
      </div>
    </div>
    <p class="footnote">† % Daily Value not established</p>
    <p class="other">Other Ingredients: Gelatin, Magnesium Stearate, and Calcium Carbonate.</p>
  </section>
</div>
</body>
</html>
```